A design led business card for the construction industry

High-end business card to match logo. White logo on dark grey/off black to the front. Matching dark font on white to back, possibly with logo design again.

We offer construction and project management services to commercial and private clients in the UK. Projetcs range from newbuilds, conversion of listed buildings and refurbishments and extensions of existing homes. Our focus is on quality and attention to detail using the highest skills.

Contact Information for Business Card

Name; Dorian Keble BSc
Position; Project Manager
Mobile; 07962 408 175
Tel; 01632 960457
email; dorian@stonevale.co.uk
web; www.stonevale.co.uk
Address; Ashcombe on Wyle, KX4 7PW

Colors

Designer to choose only greyscale colors for use in the design.

Requirements
Must have
• To include the below description of the business,

CONSTRUCTION - PROJECT MANAGEMENT
Nice to have
• The posibility of the top back of the card being used as a ruler. So will have a measurement to scale in mm or an architect scale of 1:50
Should not have
• Should not be portrait

```html
<!DOCTYPE html>
<html lang="en">
<head>
<meta charset="utf-8">
<title>Stonevale — Business Card</title>
<link href="https://fonts.googleapis.com/css2?family=Roboto:wght@300;400;500&display=swap" rel="stylesheet">
<style>
  :root {
    --stage: #1f1f1f;
    --card-dark: #2e2e2e;
    --card-light: #f4f4f4;
    --ink: #1a1a1a;
    --ink-soft: #333333;
    --rule-light: #d9d9d9;
    --band: #cfcfcf;
  }
  * { margin: 0; padding: 0; box-sizing: border-box; }
  html, body {
    width: 1200px; height: 900px; overflow: hidden;
    background: var(--stage);
    font-family: "Roboto", Arial, sans-serif;
  }
  .stage {
    width: 1200px; height: 900px;
    display: flex; flex-direction: column; align-items: center; justify-content: center;
    gap: 60px;
  }
  .card {
    position: relative; width: 600px; height: 364px; overflow: hidden;
    box-shadow: 0 18px 40px rgba(0,0,0,.45);
  }

  /* Front */
  .card--front { background: var(--card-dark); }
  .ruler { position: absolute; left: 0; top: 0; }
  .front-band {
    position: absolute; left: 0; right: 0; bottom: 0; height: 18px;
    background: var(--band);
  }
  .front-mark {
    position: absolute; left: 60px; top: 118px;
    display: flex; align-items: center; gap: 28px;
  }
  .front-mark__square {
    width: 150px; height: 150px; border: 9px solid var(--rule-light); border-radius: 6px;
  }
  .front-mark__name {
    color: var(--rule-light); font-weight: 300; font-size: 34px; letter-spacing: 12px;
  }

  /* Back */
  .card--back { background: var(--card-light); }
  .back-strip { position: absolute; left: 0; top: 0; bottom: 0; width: 22px; background: var(--card-dark); }
  .brand {
    position: absolute; right: 30px; top: 58px;
    display: flex; align-items: center; gap: 16px;
  }
  .brand__square { width: 62px; height: 62px; border: 3px solid var(--ink); flex: none; }
  .brand__text { display: flex; flex-direction: column; gap: 8px; }
  .brand__name { font-weight: 400; font-size: 22px; letter-spacing: 8px; color: var(--ink); line-height: 1; }
  .brand__tagline { font-weight: 400; font-size: 8.5px; letter-spacing: 1.6px; color: var(--ink-soft); white-space: nowrap; }
  .divider { position: absolute; left: 250px; right: 30px; top: 200px; height: 2px; background: var(--ink); }
  .person { position: absolute; left: 56px; top: 182px; }
  .person__name { font-weight: 500; font-size: 18px; color: var(--ink); letter-spacing: .3px; }
  .person__role { font-weight: 400; font-size: 12px; color: var(--ink-soft); margin-top: 2px; }
  .contacts {
    position: absolute; left: 56px; right: 24px; top: 258px;
    display: grid; grid-template-columns: 135px 180px 1fr; row-gap: 18px;
    font-size: 12px; color: var(--ink);
  }
  .contact { display: flex; align-items: center; gap: 10px; white-space: nowrap; }
  .contact svg { width: 14px; height: 14px; flex: none; }
</style>
</head>
<body>
<main class="stage">

  <section class="card card--front" aria-label="Card front">
    <svg class="ruler" width="600" height="80" viewBox="0 0 600 80" stroke="#d9d9d9" fill="#d9d9d9"
         font-family="Roboto, Arial, sans-serif" font-size="12">
      <g stroke-width="1.5">
        <line x1="30" y1="0" x2="30" y2="26"/><line x1="55" y1="0" x2="55" y2="16"/>
        <line x1="80" y1="0" x2="80" y2="26"/><line x1="105" y1="0" x2="105" y2="16"/>
        <line x1="130" y1="0" x2="130" y2="26"/><line x1="155" y1="0" x2="155" y2="16"/>
        <line x1="180" y1="0" x2="180" y2="26"/><line x1="205" y1="0" x2="205" y2="16"/>
        <line x1="230" y1="0" x2="230" y2="26"/><line x1="255" y1="0" x2="255" y2="16"/>
        <line x1="280" y1="0" x2="280" y2="26"/><line x1="305" y1="0" x2="305" y2="16"/>
        <line x1="330" y1="0" x2="330" y2="26"/><line x1="355" y1="0" x2="355" y2="16"/>
        <line x1="380" y1="0" x2="380" y2="26"/><line x1="405" y1="0" x2="405" y2="16"/>
        <line x1="430" y1="0" x2="430" y2="26"/><line x1="455" y1="0" x2="455" y2="16"/>
        <line x1="480" y1="0" x2="480" y2="26"/><line x1="505" y1="0" x2="505" y2="16"/>
        <line x1="530" y1="0" x2="530" y2="26"/>
      </g>
      <g stroke="none" text-anchor="middle">
        <text x="30" y="42">0</text><text x="80" y="42">1</text><text x="130" y="42">2</text>
        <text x="180" y="42">3</text><text x="230" y="42">4</text><text x="280" y="42">5</text>
        <text x="330" y="42">6</text><text x="380" y="42">7</text><text x="430" y="42">8</text>
        <text x="480" y="42">9</text><text x="530" y="42">10</text>
      </g>
    </svg>
    <div class="front-mark">
      <div class="front-mark__square"></div>
      <span class="front-mark__name">STONEVALE</span>
    </div>
    <div class="front-band"></div>
  </section>

  <section class="card card--back" aria-label="Card back">
    <div class="back-strip"></div>
    <div class="brand">
      <div class="brand__square"></div>
      <div class="brand__text">
        <span class="brand__name">STONEVALE</span>
        <span class="brand__tagline">CONSTRUCTION - PROJECT MANAGEMENT</span>
      </div>
    </div>
    <div class="person">
      <p class="person__name">DORIAN KEBLE BSC</p>
      <p class="person__role">Project Manager</p>
    </div>
    <div class="divider"></div>
    <div class="contacts">
      <div class="contact">
        <svg viewBox="0 0 14 14" fill="none" stroke="#1a1a1a" stroke-width="1.4"><rect x="3.5" y="1" width="7" height="12" rx="1"/><line x1="6" y1="11" x2="8" y2="11"/></svg>
        <span>07962 408 175</span>
      </div>
      <div class="contact">
        <svg viewBox="0 0 14 14" fill="none" stroke="#1a1a1a" stroke-width="1.3"><circle cx="7" cy="7" r="6"/><ellipse cx="7" cy="7" rx="2.6" ry="6"/><line x1="1" y1="7" x2="13" y2="7"/></svg>
        <span>www.stonevale.co.uk</span>
      </div>
      <div class="contact">
        <svg viewBox="0 0 14 14" fill="#1a1a1a"><path d="M7 0.5a4.5 4.5 0 0 0-4.5 4.5C2.5 8.5 7 13.5 7 13.5s4.5-5 4.5-8.5A4.5 4.5 0 0 0 7 0.5zm0 6.2a1.7 1.7 0 1 1 0-3.4 1.7 1.7 0 0 1 0 3.4z"/></svg>
        <span>Ashcombe on Wyle, KX4 7PW</span>
      </div>
      <div class="contact">
        <svg viewBox="0 0 14 14" fill="#1a1a1a"><path d="M3 1.2l2 0 1.1 3-1.4 1.1a8 8 0 0 0 3.9 3.9l1.1-1.4 3 1.1 0 2c0 .7-.6 1.2-1.3 1.2A11 11 0 0 1 1.8 2.5C1.8 1.8 2.3 1.2 3 1.2z"/></svg>
        <span>01632 960457</span>
      </div>
      <div class="contact">
        <svg viewBox="0 0 14 14" fill="none" stroke="#1a1a1a" stroke-width="1.4"><rect x="1" y="3" width="12" height="8.5"/><polyline points="1,3 7,8 13,3"/></svg>
        <span>dorian@stonevale.co.uk</span>
      </div>
    </div>
  </section>

</main>
</body>
</html>
```